Tech business card design

We need an amazing business card design for our new business 'Pexla' a marketing tech startup based in Sydney, Australia. We provide an online marketplace for businesses to search and buy advertising media, connect with service providers and learn more about marketing. We wish to communicate 'cool tech', reliability and professionalism and design based around our logo.

Target Market(s)

Business Owners

Contact Information for Business Card

Name
Position
Email Address
Website
Phone Number

Font styles to use
Other font styles liked:
• Avenir & Avenir Next

Colors

Designer to choose colors to be used in the design.

```html
<!DOCTYPE html>
<html lang="en">
<head>
<meta charset="UTF-8">
<title>Pexla Business Card</title>
<link href="https://fonts.googleapis.com/css2?family=Nunito+Sans:wght@400;600;700;900&display=swap" rel="stylesheet">
<style>
  :root {
    --backdrop: #e8e8e9;
    --navy: #1e2858;
    --navy-deep: #18214b;
    --band: #e4e5ea;
    --band-edge: #ffffff;
    --paper: #ffffff;
    --ink-light: #ffffff;
    --ink-dark: #1e2858;
    --ink-muted: #b9bfd6;
    --shadow: rgba(20, 25, 45, 0.18);
  }
  * { box-sizing: border-box; margin: 0; padding: 0; }
  html, body {
    width: 1200px;
    height: 1070px;
    overflow: hidden;
    background: var(--backdrop);
    font-family: "Nunito Sans", "Avenir Next", Avenir, sans-serif;
  }
  .canvas {
    position: relative;
    width: 1200px;
    height: 1070px;
  }
  .card {
    position: absolute;
    width: 700px;
    height: 400px;
    left: 250px;
    box-shadow: 0 14px 34px var(--shadow);
    overflow: hidden;
  }
  /* Back side */
  .card--back {
    top: 95px;
    background: var(--paper);
    display: flex;
    align-items: center;
    justify-content: center;
  }
  .card--back .wordmark {
    font-weight: 900;
    font-size: 108px;
    letter-spacing: -2px;
    color: var(--ink-dark);
  }
  /* Front side */
  .card--front {
    top: 575px;
    background: var(--navy);
  }
  .card--front .wordmark-vertical {
    position: absolute;
    left: 42px;
    top: 28px;
    font-weight: 900;
    font-size: 82px;
    letter-spacing: -1px;
    color: var(--ink-light);
    writing-mode: vertical-rl;
    line-height: 1;
  }
  .card__band {
    position: absolute;
    left: 0;
    top: 0;
    width: 700px;
    height: 400px;
  }
  .contact__name {
    position: absolute;
    left: 150px;
    top: 192px;
    font-size: 20px;
    line-height: 28px;
    font-weight: 700;
    letter-spacing: 0.3px;
    color: var(--ink-light);
    white-space: nowrap;
  }
  .contact__role {
    font-weight: 400;
    margin-left: 6px;
  }
  .contact__lines {
    position: absolute;
    left: 150px;
    top: 276px;
    display: flex;
    gap: 22px;
    font-size: 18px;
    line-height: 24px;
    color: var(--ink-dark);
    font-weight: 600;
    white-space: nowrap;
  }
  .contact__item {
    display: flex;
    align-items: center;
    gap: 8px;
  }
  .contact__item svg { width: 18px; height: 18px; fill: var(--ink-dark); }
  .website {
    position: absolute;
    right: 40px;
    bottom: 30px;
    font-size: 16px;
    color: var(--ink-muted);
    letter-spacing: 0.4px;
  }
</style>
</head>
<body>
<main class="canvas">

  <section class="card card--back" aria-label="Business card, back">
    <span class="wordmark">Pexla</span>
  </section>

  <section class="card card--front" aria-label="Business card, front">
    <svg class="card__band" viewBox="0 0 700 400" aria-hidden="true">
      <polygon points="0,270 700,236 700,320 0,354" fill="var(--band)"/>
      <polygon points="0,264 700,230 700,236 0,270" fill="var(--band-edge)" opacity="0.7"/>
      <polygon points="0,354 700,320 700,400 0,400" fill="var(--navy-deep)" opacity="0.35"/>
    </svg>

    <span class="wordmark-vertical">Pexla</span>

    <p class="contact__name">Marcus Reed<span class="contact__role">Managing Director</span></p>
    <div class="contact__lines">
      <span class="contact__item">
        <svg viewBox="0 0 24 24" aria-hidden="true"><path d="M6.6 10.8a15.1 15.1 0 0 0 6.6 6.6l2.2-2.2a1 1 0 0 1 1-.25 11.4 11.4 0 0 0 3.6.57 1 1 0 0 1 1 1V20a1 1 0 0 1-1 1A17 17 0 0 1 3 4a1 1 0 0 1 1-1h3.5a1 1 0 0 1 1 1c0 1.250.2 2.450.57 3.570a1 1 0 0 1-.25 1z"/></svg>
        000-987-6543
      </span>
      <span class="contact__item">
        <svg viewBox="0 0 24 24" aria-hidden="true"><path d="M3 5h18a1 1 0 0 1 1 1v12a1 1 0 0 1-1 1H3a1 1 0 0 1-1-1V6a1 1 0 0 1 1-1zm9 7.2L20 7H4z"/></svg>
        info@pexlamail.com
      </span>
    </div>

    <p class="website">www.pexlamail.com</p>
  </section>

</main>
</body>
</html>
```